Tidewell Health & Wellness Center Remedium

BluSketcho, Submit your previous card design as well as a couple others. Challenge yourself to make it great! You know what I want.
Updates

I would like to have a Chatterly logo beside my logo

Some designers are putting my information on the cards, but a lot are not using the information I have supplied. WHY?

I would to seed some designs on a BLACK background please, thank you.

Please include my titles "PharmD. RpH CuraLink" beside or under my name.

Industry/Entity Type

Health

Colors
add136

Requirements
Must have
• Tidewell Health & Wellness Center
Founder & President | Lou Pemberg
Bayhaven Cove Suncrest, 30214
239-555-0187
Nice to have
• I would like to have a Chatterly logo and Tidewell Health & Wellness Remedium

```html
<!DOCTYPE html>
<html lang="en">
<head>
<meta charset="utf-8">
<title>Tidewell Health &amp; Wellness Center Remedium — Business Card</title>
<link rel="stylesheet" href="https://fonts.googleapis.com/css2?family=Sorts+Mill+Goudy&display=swap">
<style>
  :root {
    --backdrop: #d9d9d9;
    --card-white: #fbfbfa;
    --brand-green: #1f8a2e;
    --brand-green-deep: #2f9a2a;
    --brand-green-light: #8ccf4a;
    --leaf-green: #5fbf3a;
    --leaf-light: #b8e27a;
    --ink-white: #ffffff;
  }
  * { box-sizing: border-box; margin: 0; padding: 0; }
  html, body {
    width: 1200px; height: 1023px; overflow: hidden;
    background: var(--backdrop);
    font-family: "Sorts Mill Goudy", Georgia, serif;
  }
  .sheet {
    width: 1200px; height: 1023px;
    display: flex; flex-direction: column; align-items: center; justify-content: center;
    gap: 48px;
  }
  .card {
    position: relative;
    width: 760px; height: 434px;
    border-radius: 4px;
    overflow: hidden;
    box-shadow: 0 6px 18px rgba(0,0,0,.18);
  }

  /* Front */
  .card-front { background: var(--card-white); }
  .leaf-cluster {
    position: absolute;
    background: radial-gradient(circle, var(--leaf-light) 0%, var(--leaf-green) 45%, rgba(95,191,58,0) 72%);
  }
  .leaf-top-left { left: -40px; top: -50px; width: 190px; height: 150px; }
  .leaf-mid-left { left: -40px; top: 200px; width: 170px; height: 170px; }
  .leaf-top-right { right: -40px; top: 120px; width: 170px; height: 140px; }
  .leaf-bottom-right { right: -30px; bottom: -40px; width: 210px; height: 190px; }

  .brand-mark {
    position: absolute; left: 50%; top: 60px; transform: translateX(-50%);
    width: 150px; height: 150px;
  }
  .brand-lockup {
    position: absolute; left: 0; right: 0; top: 228px;
    text-align: center; color: var(--brand-green);
  }
  .brand-name { font-size: 72px; line-height: 1; letter-spacing: 1px; }
  .brand-tagline { font-size: 22px; margin-top: 6px; letter-spacing: .5px; }

  /* Back */
  .card-back {
    background: radial-gradient(ellipse at 45% 55%, var(--brand-green-light) 0%, var(--brand-green-deep) 45%, #1f8a22 100%);
    color: var(--ink-white);
  }
  .back-brand { position: absolute; left: 0; right: 0; top: 30px; text-align: center; }
  .back-brand .brand-name { font-size: 74px; }
  .back-brand .brand-tagline { font-size: 24px; margin-top: 4px; }

  .contact-block {
    position: absolute; left: 60px; right: 60px; top: 205px;
    display: flex; justify-content: center;
  }
  .person { text-align: right; padding-right: 22px; border-right: 2px solid var(--ink-white); }
  .person-name { font-size: 40px; letter-spacing: 1px; text-transform: uppercase; white-space: nowrap; }
  .person-title { font-size: 22px; margin-top: 4px; }
  .details { padding-left: 22px; font-size: 28px; line-height: 1.2; white-space: nowrap; }
  .details .phone { margin-bottom: 8px; }

  .web-line {
    position: absolute; left: 0; right: 0; bottom: 34px;
    text-align: center; font-size: 30px; white-space: nowrap;
  }
  .web-line .divider { margin: 0 14px; }
</style>
</head>
<body>
<main class="sheet">

  <section class="card card-front" aria-label="Card front">
    <div class="leaf-cluster leaf-top-left" role="img" aria-label="Green leaf illustration cluster"></div>
    <div class="leaf-cluster leaf-mid-left" role="img" aria-label="Green leaf illustration cluster"></div>
    <div class="leaf-cluster leaf-top-right" role="img" aria-label="Green leaf illustration cluster"></div>
    <div class="leaf-cluster leaf-bottom-right" role="img" aria-label="Green leaf illustration cluster"></div>

    <svg class="brand-mark" viewBox="0 0 150 150" aria-hidden="true">
      <circle cx="75" cy="75" r="66" fill="none" stroke="var(--leaf-green)" stroke-width="6"/>
    </svg>

    <div class="brand-lockup">
      <div class="brand-name">Tidewell</div>
      <div class="brand-tagline">Health &amp; Wellness Center Remedium</div>
    </div>
  </section>

  <section class="card card-back" aria-label="Card back">
    <div class="back-brand">
      <div class="brand-name">Tidewell</div>
      <div class="brand-tagline">Health &amp; Wellness Center Remedium</div>
    </div>

    <div class="contact-block">
      <div class="person">
        <div class="person-name">Lou Pemberg</div>
        <div class="person-title">President &amp; Founder</div>
      </div>
      <div class="details">
        <div class="phone">239-555-0187</div>
        <div class="address">Bayhaven Cove<br>Suncrest, 30214</div>
      </div>
    </div>

    <div class="web-line">
      <span class="website">www.tidewellhealth.com</span><span class="divider">|</span><span class="email">lou@tidewellhealth.com</span>
    </div>
  </section>

</main>
</body>
</html>
```